BRAMBLEFORD CONSTRUCTIONS B-Card

I currently have a b-card design but will be removing the image (tree) from the logo and have text only.
I want the card to be classy and strong within the building and construction industry.
I will be using Spot UV on the cards as per the attached examples. I will also send through some sketched ideas that I have in mind.
The color blue is similar to the image (No. 6) attached images

Target Market(s)

middle to maturre aged.
Home Owners / Renovators and Builders

Industry/Entity Type

Construction

Contact Information for Business Card

BRAMBLEFORD CONSTRUCTIONS
Name: Gareth Pennick
Title: Project Manager
Mobile: 0427 351 804
Office: (08) 9316 5172
Address: 47C Corvell Street, Malaga WA 6090
Email: info@bramblefordhomes.com.au
PO Box: 3817 Malaga WA 6944

Colors
0592cd
33a6d7
85cae6
1b1b1b

Requirements
Must have
• 1. It must have spot UV on the front of card, maybe back of card too
• 2. I really like the blue on image 6. (or at least a really cool electric blue against the charcoal grey background)
• 3. The font must be slimline and modern. Easy to read
• 4. There must be no black used on the card... Only greys and dark charcoal greys
• 5. Use only the text from the logo "Brambleford Constructions" Not the image of the tree. I am wanting the b-cards to be more masculine.
Nice to have
• 1. I like the design concept on image 6. but happy to see what else you can do with the Spot UV
• 2. Unless you have a really cool idea of the image of the tree (from previous logo) Spot UV somewhere in the design concept thats original and different then I am keen to see what you come up with
• 3. Try changing the color of the logo eg. full white or Blue and white
• 4. Another option is to have the Brambleford Logo on the front of card with the spot UV in the background of text which we specialise in eg, Roofing, Ceiling, Insulation, Gutter Guards, Electrical, Insurance etc and we can add or reduce items as required. Similar to image 12.
Should not have
• Do not include the image of the tree from previous logo. unless you have a really cool idea of Spot UV somewhere in the design concept thats original and different.

```html
<!DOCTYPE html>
<html lang="en">
<head>
<meta charset="utf-8">
<title>Brambleford Constructions Business Card</title>
<link href="https://fonts.googleapis.com/css2?family=Jost:wght@400;500;600&display=swap" rel="stylesheet">
<style>
  :root {
    --page-bg: #e6e4e0;
    --brand-blue: #1d5fae;
    --charcoal: #262728;
    --paper: #ffffff;
    --text-light: #f2f2f2;
    --text-muted: #d8d8d8;
    --card-shadow: 0 10px 28px rgba(40, 36, 30, 0.28);
  }
  * { box-sizing: border-box; margin: 0; padding: 0; }
  html, body {
    width: 1200px;
    height: 843px;
    overflow: hidden;
  }
  body {
    background: var(--page-bg);
    font-family: "Jost", sans-serif;
    position: relative;
  }
  .card {
    position: absolute;
    left: 280px;
    width: 640px;
    height: 366px;
    box-shadow: var(--card-shadow);
    overflow: hidden;
  }

  /* Back of card */
  .card-back {
    top: 36px;
    background: var(--brand-blue);
  }
  .card-back .spot-uv-field {
    position: absolute;
    inset: 0;
    background: linear-gradient(135deg, rgba(255,255,255,0.05), rgba(0,0,0,0.06) 50%, rgba(255,255,255,0.05));
  }
  .services {
    position: absolute;
    left: 250px;
    top: 128px;
    color: var(--text-light);
    font-size: 21px;
    font-weight: 400;
    line-height: 1.35;
    letter-spacing: 0.3px;
  }
  .services .line-one { padding-left: 38px; }

  /* Front of card */
  .card-front {
    top: 440px;
    background: var(--paper);
  }
  .front-top {
    position: absolute;
    left: 0; top: 0;
    width: 100%;
    height: 168px;
    background: var(--paper);
    display: flex;
    align-items: center;
    justify-content: flex-end;
    padding-right: 40px;
  }
  .company-name {
    color: var(--brand-blue);
    font-size: 38px;
    font-weight: 500;
    line-height: 1;
  }
  .name-band {
    position: absolute;
    left: 0; top: 168px;
    width: 100%;
    height: 44px;
    background: var(--brand-blue);
    display: flex;
    align-items: center;
    padding-left: 108px;
    color: var(--paper);
    font-size: 22px;
  }
  .name-band .person-name { font-weight: 600; }
  .name-band .person-role { font-weight: 400; margin-left: 8px; }
  .front-bottom {
    position: absolute;
    left: 0; top: 212px;
    width: 100%;
    height: 154px;
    background: var(--charcoal);
    color: var(--text-light);
  }
  .contact-list {
    list-style: none;
    position: absolute;
    left: 22px;
    top: 16px;
    font-size: 15px;
    line-height: 1.55;
    color: var(--text-muted);
  }
  .contact-list li {
    display: flex;
    align-items: center;
    gap: 9px;
  }
  .contact-list svg {
    width: 13px;
    height: 13px;
    fill: var(--text-light);
    flex: none;
  }
  .address {
    position: absolute;
    right: 26px;
    bottom: 20px;
    text-align: right;
    font-style: normal;
    font-size: 17px;
    line-height: 1.35;
    color: var(--text-light);
  }
</style>
</head>
<body>

  <section class="card card-back" aria-label="Back of business card">
    <div class="spot-uv-field" role="img" aria-label="Spot UV background of repeated company name in tone-on-tone blue"></div>
    <p class="services">
      <span class="line-one">Roofing | Ceiling | Insulation</span><br>
      Gutter Guards | Electrical | Insurance etc
    </p>
  </section>

  <section class="card card-front" aria-label="Front of business card">
    <div class="front-top">
      <h1 class="company-name">Brambleford Constructions</h1>
    </div>

    <div class="name-band">
      <span class="person-name">Gareth Pennick -</span>
      <span class="person-role">Project Manager</span>
    </div>

    <div class="front-bottom">
      <ul class="contact-list">
        <li>
          <svg viewBox="0 0 16 16" aria-hidden="true"><path d="M3.6 1.2l2.2 2.6c.3.4.3.9 0 1.3L4.7 6.3c.9 2 2.6 3.8 4.8 4.9l1.2-1.1c.4-.3.9-.3 1.3 0l2.6 2.2c.4.4.4 1 0 1.4l-1.3 1.2C11.9 16 3.2 11 .3 3.2c-.3-.6 0-1.2.5-1.6L2.2.9c.4-.1 1.1-.1 1.4.3z"/></svg>
          <span>(08) 9316 5172</span>
        </li>
        <li>
          <svg viewBox="0 0 16 16" aria-hidden="true"><path d="M4.5 0h7c.8 0 1.5.7 1.5 1.5v13c0 .8-.7 1.5-1.5 1.5h-7C3.7 16 3 15.3 3 14.5v-13C3 .7 3.7 0 4.5 0zm.5 2v10h6V2H5zm3 11.2a.9.9 0 100 1.8.9.9 0 000-1.8z"/></svg>
          <span>0427 351 804</span>
        </li>
        <li>
          <svg viewBox="0 0 16 16" aria-hidden="true"><path d="M0 3h16v10H0V3zm1.6 1.3L8 9l6.4-4.7H1.6zM1.3 5.4v6.3h13.4V5.4L8 10.5 1.3 5.4z"/></svg>
          <span>info@bramblefordhomes.com.au</span>
        </li>
      </ul>

      <address class="address">
        47C Corvell Street<br>
        Tarrenvale WA 6137<br>
        PO Box: 3817 Tarrenvale WA 6952
      </address>
    </div>
  </section>

</body>
</html>
```